Brenwick Structures Construction Company Seeking Modern Website

We are a small construction company wanting to create a web presence. We don't have much in the way of current content but will get photos as they come in. Attached is a picture of our business card.
The pages we would like on the menu are:
Home
Portfolio
Product Specs
Testimonials
Our Process
Contact
Some designs we like are:
http://www.tovasheds-example.com/
http://www.qrnstructures-example.com/
http://dunholtbarns-example.com/
http://pellingframes-example.com/
Not much requirements other than that so feel free to be creative!
Updates
Target Market(s)
Construction
Commercial and Residential Buildings
Industry/Entity Type
Construction Company
Number of Pages Required
5+ page
Look and feel

```html
<!DOCTYPE html>
<html lang="en">
<head>
<meta charset="utf-8">
<title>Brenwick Structures</title>
<link href="https://fonts.googleapis.com/css2?family=Roboto:wght@300;400;500;700&family=Open+Sans:wght@400;700&display=swap" rel="stylesheet">
<style>
:root{
  --blue:#1a9fd9;
  --footer:#16b0e2;
  --red:#d9412b;
  --text:#555b61;
  --page:#f2f3f6;
  --grey-band:#b5b5b5;
  --white:#fff;
}
*{box-sizing:border-box;margin:0;padding:0}
html,body{width:821px;height:1200px;overflow:hidden}
body{background:var(--page);font-family:'Roboto',sans-serif;position:relative;color:var(--text)}
.page-curve{position:absolute;left:-200px;top:-300px;width:1221px;height:740px;border-radius:50%;background:var(--white)}
.site{position:absolute;left:102px;top:0;width:614px;height:1200px}
.abs{position:absolute}

/* header */
.header{left:0;top:0;width:614px;height:106px;background:var(--white)}
.brand{left:21px;top:26px;font:700 22px 'Roboto',sans-serif;color:var(--blue);letter-spacing:-.3px}
.follow{left:345px;top:26px;font-size:7px;color:#888;letter-spacing:.3px}
.follow .dots{display:flex;gap:10px;margin-top:6px;padding-left:3px}
.follow .dots span{width:9px;height:9px;border-radius:50%;background:var(--blue)}
.call{left:425px;top:26px;font-size:7px;color:#888;letter-spacing:.3px}
.call b{display:block;font:400 11px 'Roboto',sans-serif;color:var(--blue);margin-top:5px;letter-spacing:0}
.search{left:529px;top:25px;width:71px;height:25px;border:1px solid #ddd;font-size:7px;color:#888;padding:8px 7px;letter-spacing:.3px}
.search svg{position:absolute;right:8px;top:8px}
.nav{left:0;top:78px;width:614px;height:28px;border-top:1px solid #e6e6e6;display:flex;align-items:center;font:400 8px 'Roboto',sans-serif;color:#333;letter-spacing:.2px}
.nav a{text-decoration:none;color:inherit;height:16px;line-height:16px;text-align:center;border-right:1px solid #ddd}
.nav a:last-child{border:none}
.nav a.active{color:var(--blue)}

/* hero */
.hero{left:0;top:106px;width:614px;height:326px;background:linear-gradient(180deg,#3a9de8 0%,#8ac7f2 35%,#6b7a5c 58%,#5a9a2e 78%,#8fc43a 100%)}
.hero-caption{left:208px;top:212px;width:200px;height:116px;background:rgba(60,60,60,.55);color:#fff;font:300 20px/28px 'Roboto',sans-serif;text-align:center;padding-top:10px}
.hero-dots{left:264px;top:400px;display:flex;gap:12px;align-items:center}
.hero-dots span{width:7px;height:7px;border-radius:50%;background:#fff}
.hero-dots span.on{width:9px;height:9px;background:none;border:1.5px solid #fff}

/* services */
.service{top:432px;width:307px;height:181px;background:var(--white);overflow:hidden}
.service h2{position:absolute;left:29px;top:32px;font:400 14.5px 'Roboto',sans-serif;color:var(--blue)}
.service p{position:absolute;left:30px;top:59px;width:160px;font-size:8.5px;line-height:14px;white-space:nowrap}
.service .more{position:absolute;left:31px;top:128px;font:700 8px 'Roboto',sans-serif;color:var(--red);letter-spacing:1.2px}
.service .photo{position:absolute}

/* portfolio */
.portfolio{left:0;top:613px;width:614px;height:211px;background:var(--white)}
.sec-title{position:absolute;font:400 14.5px 'Roboto',sans-serif}
.arrows{position:absolute;display:flex;gap:5px}
.arrows span{width:18px;height:18px;background:#e4e4e4;display:flex;align-items:center;justify-content:center}
.tile{position:absolute;top:51px;width:188px;height:139px}
.tile .cap{position:absolute;left:0;bottom:0;width:100%;height:37px;background:rgba(20,20,20,.6);color:#fff;padding:9px 11px 0;font-family:'Open Sans',sans-serif}
.tile .cap b{display:block;font-size:8.5px;line-height:11px;letter-spacing:.3px}
.tile .cap span{display:block;font-size:8px;line-height:11px;color:#ddd}

/* testimonials */
.testimonials{left:0;top:824px;width:614px;height:190px;background:var(--grey-band)}
.quote{position:absolute;top:48px;width:280px;height:123px;background:var(--white);border-radius:2px}
.quote svg{position:absolute;left:14px;top:12px}
.quote p{position:absolute;left:22px;top:33px;width:250px;font-size:8.5px;line-height:14px;white-space:nowrap}
.author{position:absolute;left:20px;top:94px;display:flex;align-items:center;gap:6px;font-size:8.5px;color:var(--blue)}
.author i{width:16px;height:16px;border-radius:50%;background:#c9c2bb;display:block}
.author small{font-size:7px;color:#555}

/* footer */
.footer{left:0;top:1014px;width:614px;height:186px;background:var(--footer);color:#fff}
.fcol{position:absolute;top:20px}
.fcol h3{font:500 12px 'Roboto',sans-serif;margin-bottom:10px}
.fcol li{list-style:none;font-size:8px;line-height:15.2px}
.social li{display:flex;align-items:center;gap:8px;line-height:19px}
.social li i{width:9px;height:9px;border-radius:50%;background:#fff;display:block}
.signup{position:absolute;left:0;top:43px;display:flex}
.signup .field{width:118px;height:31px;background:#fff;color:#666;font-size:8px;padding:11px 10px;display:flex;gap:7px;align-items:flex-start}
.signup .btn{width:60px;height:31px;background:var(--red);font:700 9px 'Roboto',sans-serif;letter-spacing:1px;display:flex;align-items:center;justify-content:center}
.footer-rule{position:absolute;left:0;top:151px;width:614px;border-top:1px solid rgba(255,255,255,.2)}
.copyright{position:absolute;right:24px;top:163px;font-size:7.5px}
</style>
</head>
<body>
<div class="page-curve"></div>
<div class="site">

  <header class="abs header">
    <div class="abs brand">Brenwick Structures</div>
    <div class="abs follow">FOLLOW US ON<div class="dots"><span></span><span></span><span></span></div></div>
    <div class="abs call">
      <svg width="6" height="6" viewBox="0 0 10 10"><path d="M2 1l2 2-1 1.5c.7 1.4 1.7 2.4 3 3L7.5 6l2 2-1.2 1.5C4.5 9 1 5.5.5 1.7z" fill="#888"/></svg>
      CALL US TODAY!<b>555.0142.730</b></div>
    <div class="abs search">SEARCH
      <svg width="8" height="8" viewBox="0 0 10 10"><circle cx="4" cy="4" r="3" stroke="#888" fill="none" stroke-width="1.3"/><path d="M6.3 6.3L9 9" stroke="#888" stroke-width="1.3"/></svg>
    </div>
    <nav class="abs nav">
      <a class="active" href="#" style="width:75px">HOME</a>
      <a href="#" style="width:95px">PORTFOLIO</a>
      <a href="#" style="width:127px">PRODUCT SPECS</a>
      <a href="#" style="width:114px">TESTIMONIALS</a>
      <a href="#" style="width:113px">OUR PROCESS</a>
      <a href="#" style="width:90px">CONTACT</a>
    </nav>
  </header>

  <section class="abs hero" role="img" aria-label="Photo of a large stone-and-siding suburban house with a green lawn under a blue sky"></section>
  <div class="abs hero-caption">Building Dreams,<br>So you can Build<br>Memories</div>
  <div class="abs hero-dots"><span></span><span></span><span class="on"></span><span></span><span></span></div>

  <article class="abs service" style="left:0">
    <div class="photo" role="img" aria-label="Photo of glass and concrete high-rise towers" style="left:190px;top:0;width:117px;height:181px;background:linear-gradient(90deg,#f4f1ec 0%,#c9a680 40%,#3a78b8 75%,#2a5f98 100%)"></div>
    <h2>Commercial Construction</h2>
    <p>There are many variations of<br>passages of Lorem Ipsum available,<br>but the majority have suffered<br>alteration in some form.</p>
    <div class="more">READ MORE</div>
  </article>
  <article class="abs service" style="left:308px">
    <div class="photo" role="img" aria-label="Photo of a cream two-storey house with flower boxes" style="left:190px;top:0;width:117px;height:181px;background:linear-gradient(180deg,#f4f2ee 0%,#e6dfd2 45%,#cfc4b2 80%,#8a9a6a 100%)"></div>
    <h2>Residential Buildings</h2>
    <p>It is a long established fact that a<br>reader will be distracted by the<br>readable content of a page when<br>ooking at its layout.</p>
    <div class="more">READ MORE</div>
  </article>

  <section class="abs portfolio">
    <h2 class="sec-title" style="left:14px;top:22px;color:var(--blue)">Portfolio</h2>
    <div class="arrows" style="left:558px;top:21px">
      <span><svg width="6" height="8" viewBox="0 0 6 8"><path d="M5 0L1 4l4 4" stroke="#555" fill="none"/></svg></span>
      <span><svg width="6" height="8" viewBox="0 0 6 8"><path d="M1 0l4 4-4 4" stroke="#555" fill="none"/></svg></span>
    </div>
    <div class="tile" style="left:16px;background:linear-gradient(180deg,#c5ccd3 0%,#8d8f92 35%,#8a4a3a 65%,#4d5a3a 100%)" role="img" aria-label="Photo of a brick cape-cod house">
      <div class="cap"><b>HEADING 1</b><span>There are many variations</span></div></div>
    <div class="tile" style="left:215px;background:linear-gradient(180deg,#8aa7c8 0%,#b44a2c 30%,#e9e9e6 55%,#3d5a30 100%)" role="img" aria-label="Photo of a white colonial house with autumn trees">
      <div class="cap"><b>HEADING 2</b><span>There are many variations</span></div></div>
    <div class="tile" style="left:414px;background:linear-gradient(180deg,#4f8fd8 0%,#9cc0e6 25%,#e6e0b8 55%,#4b6b3a 100%)" role="img" aria-label="Photo of a pale yellow two-storey house">
      <div class="cap"><b>HEADING 3</b><span>There are many variations</span></div></div>
  </section>

  <section class="abs testimonials">
    <h2 class="sec-title" style="left:19px;top:18px;color:#fff;font-weight:500">Testimonials</h2>
    <div class="arrows" style="left:558px;top:16px">
      <span style="background:#fff"><svg width="6" height="8" viewBox="0 0 6 8"><path d="M5 0L1 4l4 4" stroke="#555" fill="none"/></svg></span>
      <span style="background:#fff"><svg width="6" height="8" viewBox="0 0 6 8"><path d="M1 0l4 4-4 4" stroke="#555" fill="none"/></svg></span>
    </div>
    <div class="quote" style="left:22px">
      <svg width="18" height="14" viewBox="0 0 18 14"><path d="M0 7Q0 1 6 0v2Q3 3 3 6h4v8H0zM10 7q0-6 6-7v2q-3 1-3 4h4v8h-7z" fill="#d0d0d0"/></svg>
      <p>There are many variations of passages of Lorem Ipsum<br>available, but the majority have suffered alteration in some<br>form. combined with a handful of model sentence structures,<br>to generate Lorem Ipsum</p>
      <div class="author"><i></i>Dalia Remsford <small>Sydney</small></div>
    </div>
    <div class="quote" style="left:316px">
      <svg width="18" height="14" viewBox="0 0 18 14"><path d="M0 7Q0 1 6 0v2Q3 3 3 6h4v8H0zM10 7q0-6 6-7v2q-3 1-3 4h4v8h-7z" fill="#d0d0d0"/></svg>
      <p>Lorem Ipsum is simply dummy text of the printing and<br>typesetting industry. Lorem Ipsum has been the industry's<br>standard dummy text ever since the 1500s, when an<br>unknown printer took only five centuries,</p>
      <div class="author"><i></i>Dalia Remsford <small>Sydney</small></div>
    </div>
  </section>

  <footer class="abs footer">
    <div class="fcol" style="left:22px"><h3>Contact Us</h3><ul>
      <li>418 Corvale Lane, Maplewood,</li><li>PA 15230.</li><li>t : 1.555.0142.730</li><li>E : info@brenwick-example.com</li></ul></div>
    <div class="fcol" style="left:188px"><h3>Menu</h3><ul>
      <li>Home</li><li>Portfolio</li><li>Product Specs</li><li>Testimonials</li><li>Our Process</li><li>Contact</li></ul></div>
    <div class="fcol social" style="left:302px"><h3>Follow us on</h3><ul>
      <li><i></i>Linkora</li><li><i></i>Chirply</li><li><i></i>Circlet</li></ul></div>
    <div class="fcol" style="left:413px;width:180px"><h3>Newsletter Subscribe</h3>
      <div style="font-size:8px">Get more Details!</div>
      <div class="signup">
        <div class="field"><svg width="9" height="7" viewBox="0 0 9 7"><rect width="9" height="7" fill="#bbb"/><path d="M0 0l4.5 4L9 0" stroke="#fff" fill="none"/></svg>E mail id</div>
        <div class="btn">SIGNUP!</div>
      </div>
    </div>
    <div class="footer-rule"></div>
    <div class="copyright">Copyrights @ 2015 All Rihgts Reserved</div>
  </footer>
</div>
</body>
</html>
```